we can communicate on this, but i want to follow the approach we took on Pellew|Marsh & Quinlan but i feel the card front needs the black background and the platinum and gold logo. The back? I am open. we can use the same info from PM&Q. Velmont Arc is an enhanced equity investment fund - basically a very exclusive boutique hedge fund that uses only stock options. very advanced things. hope you are interested

Contact Information for Business Card

Dr. Lewis T. Brennick, CFA
Scientifique de fusée financière
701.555.0143
LTBquant47@mailvantor.com

4718 Willow Creek Bend W.
West Fargo, ND 58078

No web site

Colors

Designer to choose colors to be used in the design.

Requirements
Nice to have
• I tend to prefer the most visible applications of the logo to include logo and name, the logo version with a black background and the gold and platinum components separated by the black. I see this working well for a single side (logo and name - this is card front to me).
• I am fairly open to other treatments on the reverse side with the data. To me, it makes sense to have a different color rendition of the logo on the reverse and it may be a muted black tone on tone or an oversized portion that would have spot UV. Or, the reverse may play with colors and layout
Should not have
• Other colors = no no
• Decorative font

```html
<!DOCTYPE html>
<html lang="en">
<head>
<meta charset="utf-8">
<title>Velmont Arc — Business Card</title>
<link rel="stylesheet" href="https://fonts.googleapis.com/css2?family=Montserrat:wght@700&family=Ubuntu:wght@400;500&display=swap">
<style>
  :root{
    --stage:#3b3b3d;
    --card:#232325;
    --white:#f4f4f4;
    --gold:#d6ad2a;
    --gold-light:#ecd65a;
    --gold-dark:#b48a16;
    --silver-light:#e6e6e8;
    --silver-dark:#6c6c70;
  }
  *{margin:0;padding:0;box-sizing:border-box}
  html,body{width:799px;height:1200px;overflow:hidden}
  body{background:var(--stage);position:relative;font-family:"Ubuntu",sans-serif}
  .card{
    position:absolute;left:80px;width:640px;height:366px;
    background:var(--card);overflow:hidden;
    box-shadow:0 8px 24px rgba(0,0,0,.35);
  }
  .card--front{top:118px}
  .card--back{top:716px}

  /* Brand lockup */
  .brand{position:absolute;display:flex;flex-direction:column;align-items:center}
  .brand__dot{border-radius:50%;background:linear-gradient(135deg,var(--gold-light),var(--gold) 55%,var(--gold-dark))}
  .brand__name{
    font-family:"Montserrat",sans-serif;font-weight:700;color:var(--white);
    text-align:center;line-height:1.05;letter-spacing:1px;text-transform:uppercase;
    white-space:nowrap;
  }
  .card--front .brand{left:0;right:0;top:72px}
  .card--front .brand__dot{width:112px;height:112px;margin-bottom:22px}
  .card--front .brand__name{font-size:50px}

  .card--back .brand{left:30px;top:44px;width:280px}
  .card--back .brand__dot{width:86px;height:86px;margin-bottom:14px}
  .card--back .brand__name{font-size:30px}

  /* Contact block */
  .contact{position:absolute;left:350px;top:84px;color:var(--white);font-size:15px}
  .contact__name{color:var(--gold);font-weight:500;font-size:20px;white-space:nowrap}
  .contact__role{font-size:14px;margin:2px 0 16px}
  .contact__line{display:flex;align-items:center;gap:10px;margin-bottom:6px;white-space:nowrap}
  .contact__line svg{width:16px;height:14px;flex:none}
  .contact__address{margin-top:6px;line-height:1.35}

  .bands{position:absolute;left:0;bottom:0;width:640px;height:110px}
</style>
</head>
<body>

<section class="card card--front" aria-label="Card front">
  <div class="brand">
    <span class="brand__dot" aria-hidden="true"></span>
    <span class="brand__name">Velmont Arc</span>
  </div>
</section>

<section class="card card--back" aria-label="Card back">
  <div class="brand">
    <span class="brand__dot" aria-hidden="true"></span>
    <span class="brand__name">Velmont Arc</span>
  </div>

  <div class="contact">
    <p class="contact__name">Dr. Lewis T. Brennick, CFA</p>
    <p class="contact__role">Scientifique de fusée financière</p>
    <p class="contact__line">
      <svg viewBox="0 0 16 14" aria-hidden="true"><path fill="var(--gold)" d="M2 4c0-2 2-3 6-3s6 1 6 3v1h-3V4H5v1H2zM4 6h8l2 7H2z"/></svg>
      701.555.0143
    </p>
    <p class="contact__line">
      <svg viewBox="0 0 16 14" aria-hidden="true"><rect x="1" y="2" width="14" height="10" fill="var(--gold)"/><path d="M1 2l7 6 7-6" fill="none" stroke="var(--card)" stroke-width="1.4"/></svg>
      LTBquant47@mailvantor.com
    </p>
    <p class="contact__address">4718 Willow Creek Bend W.<br>West Fargo, ND 58078</p>
  </div>

  <svg class="bands" viewBox="0 0 640 110" aria-hidden="true">
    <defs>
      <linearGradient id="silver" x1="0" x2="1" y1="0" y2="0">
        <stop offset="0" stop-color="var(--silver-light)"/>
        <stop offset="1" stop-color="var(--silver-dark)"/>
      </linearGradient>
      <linearGradient id="gold" x1="0" x2="1" y1="0" y2="1">
        <stop offset="0" stop-color="var(--gold-dark)"/>
        <stop offset=".45" stop-color="var(--gold-light)"/>
        <stop offset="1" stop-color="var(--gold-dark)"/>
      </linearGradient>
    </defs>
    <path d="M0 6 H290 L330 34 V44 L286 16 H0 Z" fill="url(#silver)"/>
    <path d="M300 110 V58 Q300 34 326 34 H640 V110 Z" fill="url(#gold)"/>
  </svg>
</section>

</body>
</html>
```